KBT Business Cards

We require business cards for our business. We would like a matte black back to the card, with our logo centred in the middle. The front side of the card is open to design.

Target Market(s)

Clients looking for legal services (professional)

Industry/Entity Type

Legal

Contact Information for Business Card

Doran Kelbrath
Partner
Mobile: 0461 738 524
Email: doran@kbtlaw.co
Website: www.kbtlaw.co
Level 3, 118 Wendmore Street
Sydney NSW 2000

Font styles to use
Other font styles liked:
• Avenir

Colors
f04a50
ffffff
1b1b1b

Requirements
Must have
• Black back with logo included in the centre of the card.
• Our font is Avenir.

```html
<!DOCTYPE html>
<html lang="en">
<head>
<meta charset="utf-8">
<title>KBT Business Cards</title>
<link rel="stylesheet" href="https://fonts.googleapis.com/css2?family=Roboto:wght@400;500;700&display=swap">
<style>
  :root {
    --brand-red: #d4234a;
    --brand-red-deep: #8e1c35;
    --ink: #1b1b1b;
    --card-black: #231f20;
    --text-grey: #555555;
    --paper: #ffffff;
    --backdrop: #e4e4e4;
    --rule: #d6d6d6;
  }
  * { margin: 0; padding: 0; box-sizing: border-box; }
  html, body {
    width: 1125px;
    height: 1200px;
    overflow: hidden;
    background: var(--backdrop);
    font-family: "Roboto", Arial, sans-serif;
  }
  .sheet { position: relative; width: 1125px; height: 1200px; }

  .card {
    position: absolute;
    left: 171px;
    width: 826px;
    height: 471px;
    overflow: hidden;
  }
  .card--front { top: 106px; background: var(--paper); }
  .card--back  { top: 639px; background: var(--card-black); }

  /* Front: firm name block */
  .firm-mark {
    position: absolute;
    left: 126px;
    top: 213px;
    width: 52px;
    height: 52px;
    background: var(--brand-red);
  }
  .firm-name {
    position: absolute;
    left: 210px;
    top: 192px;
    font-weight: 500;
    font-size: 27px;
    line-height: 29px;
    color: var(--ink);
    text-transform: uppercase;
  }

  .divider {
    position: absolute;
    left: 415px;
    top: 115px;
    width: 1px;
    height: 250px;
    background: linear-gradient(to bottom, rgba(0,0,0,0), var(--rule) 20%, var(--rule) 80%, rgba(0,0,0,0));
  }

  /* Front: contact column */
  .contact { position: absolute; left: 446px; top: 124px; }
  .contact__name {
    font-weight: 700;
    font-size: 30px;
    line-height: 34px;
    color: var(--brand-red);
  }
  .contact__role {
    font-weight: 500;
    font-size: 20px;
    line-height: 24px;
    color: var(--ink);
  }
  .contact__address {
    margin-top: 12px;
    font-size: 19.5px;
    line-height: 25px;
    color: var(--text-grey);
  }
  .contact__list { list-style: none; margin-top: 17px; }
  .contact__item {
    display: flex;
    align-items: center;
    font-size: 19.5px;
    line-height: 26px;
    color: var(--text-grey);
  }
  .contact__icon { width: 20px; height: 18px; margin-right: 12px; flex: none; }

  .front-band { position: absolute; left: 0; bottom: 0; width: 826px; height: 15px; }

  /* Back */
  .back-mark {
    position: absolute;
    left: 385px;
    top: 130px;
    width: 56px;
    height: 56px;
    background: var(--brand-red);
  }
  .back-name {
    position: absolute;
    left: 0;
    width: 100%;
    top: 212px;
    text-align: center;
    font-weight: 500;
    font-size: 34px;
    line-height: 40px;
    color: var(--paper);
    text-transform: uppercase;
  }
  .back-web {
    position: absolute;
    left: 0;
    width: 100%;
    top: 398px;
    text-align: center;
    font-size: 18px;
    letter-spacing: 0.95em;
    padding-left: 0.95em;
    color: var(--paper);
    text-transform: uppercase;
  }
</style>
</head>
<body>
<main class="sheet">

  <section class="card card--front" aria-label="Business card front">
    <span class="firm-mark" aria-hidden="true"></span>
    <div class="firm-name">Kelbrath<br>Brandt<br>Tovey</div>

    <span class="divider" aria-hidden="true"></span>

    <div class="contact">
      <h1 class="contact__name">Doran Kelbrath</h1>
      <p class="contact__role">Partner</p>
      <p class="contact__address">Level 3, 118 Wendmore Street<br>Sydney NSW 2000</p>
      <ul class="contact__list">
        <li class="contact__item">
          <svg class="contact__icon" viewBox="0 0 20 18" aria-hidden="true">
            <rect x="5" y="0.5" width="10" height="17" rx="1.5" fill="none" stroke="var(--brand-red)" stroke-width="2"/>
            <rect x="8" y="14" width="4" height="1.5" fill="var(--brand-red)"/>
          </svg>0461 738 524
        </li>
        <li class="contact__item">
          <svg class="contact__icon" viewBox="0 0 20 18" aria-hidden="true">
            <rect x="1" y="5" width="18" height="11" fill="var(--brand-red)"/>
            <path d="M1 5 L10 11.5 L19 5" fill="none" stroke="var(--paper)" stroke-width="1.4"/>
          </svg>doran@kbtlaw.co
        </li>
        <li class="contact__item">
          <svg class="contact__icon" viewBox="0 0 20 18" aria-hidden="true">
            <circle cx="10" cy="9" r="8.5" fill="var(--brand-red)"/>
            <path d="M4 5 Q7 6 8 9 Q7 12 9 15 M13 3 Q12 6 15 8 Q17 9 16 13" fill="none" stroke="var(--paper)" stroke-width="1.6"/>
          </svg>www.kbtlaw.co
        </li>
      </ul>
    </div>

    <svg class="front-band" viewBox="0 0 826 15" preserveAspectRatio="none" aria-hidden="true">
      <defs>
        <linearGradient id="band-red" x1="0" x2="1" y1="0" y2="0">
          <stop offset="0" stop-color="var(--brand-red-deep)"/>
          <stop offset="0.55" stop-color="var(--brand-red)"/>
          <stop offset="1" stop-color="var(--brand-red-deep)"/>
        </linearGradient>
      </defs>
      <polygon points="0,0 535,0 530,15 0,15" fill="url(#band-red)"/>
      <polygon points="539,0 826,0 826,15 534,15" fill="var(--ink)"/>
    </svg>
  </section>

  <section class="card card--back" aria-label="Business card back">
    <span class="back-mark" aria-hidden="true"></span>
    <div class="back-name">Kelbrath Brandt Tovey</div>
    <p class="back-web">www.kbtlaw.co</p>
  </section>

</main>
</body>
</html>
```